Harborline Renewal Business Card Design

Professional and clean design. The design colors should flow with the logo. Two-sided card with the website on the back which is:

www.HarborlineRenewal.example.

"Specializing in Water Damage Restoration"

On the front I need the name, email, phone, and logo.

Name: Darnell Quisby
Email: Darnell@HarborlineRenewal.example
Phone: 555-318-2046 for now

I only have the Preview and Thumbnail right now but should have the source files uploaded within a day or two.

Target Market(s)

Flood victims, home owners with water damage from busted pipes etc...

Industry/Entity Type

Business

Contact Information for Business Card

Name: Darnell Quisby

Font styles to use
Serif
Sans Serif

Requirements
Must have
• Business Card Details Info

```html
<!DOCTYPE html>
<html lang="en">
<head>
<meta charset="utf-8">
<title>Harborline Renewal – Business Card</title>
<link rel="stylesheet" href="https://fonts.googleapis.com/css2?family=Cinzel:wght@400;600;700&family=Open+Sans:wght@400;600&display=swap">
<style>
  :root {
    --sky: #58c0ef;
    --ocean: #2b93d6;
    --brand: #2a86c4;
    --ink: #1f2a33;
    --paper: #ffffff;
    --backdrop: #e9edf0;
  }
  * { margin: 0; padding: 0; box-sizing: border-box; }
  html, body {
    width: 1200px;
    height: 1120px;
    overflow: hidden;
    background: var(--backdrop);
  }
  .canvas {
    position: relative;
    width: 1200px;
    height: 1120px;
  }
  .card {
    position: absolute;
    left: 160px;
    width: 880px;
    height: 503px;
    overflow: hidden;
    box-shadow: 0 6px 18px rgba(0,0,0,0.18);
  }
  .card-back { top: 36px; background: var(--sky); }
  .card-front { top: 579px; background: var(--paper); }

  /* back side */
  .back-mark {
    position: absolute;
    left: 340px;
    top: 50px;
    width: 200px;
    height: 200px;
    border-radius: 50%;
    background: var(--paper);
  }
  .back-name {
    position: absolute;
    left: 0; right: 0;
    top: 282px;
    text-align: center;
    font-family: "Cinzel", serif;
    font-weight: 700;
    font-size: 40px;
    letter-spacing: 1px;
    color: var(--paper);
  }
  .tagline {
    position: absolute;
    left: 0; right: 0;
    top: 400px;
    text-align: center;
    font-family: "Cinzel", serif;
    font-weight: 400;
    font-size: 25px;
    letter-spacing: 1px;
    color: var(--paper);
  }

  /* front side */
  .front-art { position: absolute; inset: 0; width: 880px; height: 503px; }
  .front-mark {
    position: absolute;
    left: 400px;
    top: 40px;
    width: 80px;
    height: 80px;
    border-radius: 50%;
    background: var(--sky);
  }
  .company-name {
    position: absolute;
    left: 0; right: 0;
    top: 135px;
    text-align: center;
    font-family: "Cinzel", serif;
    font-weight: 700;
    font-size: 42px;
    color: var(--brand);
  }
  .person {
    position: absolute;
    left: 460px;
    width: 270px;
    top: 248px;
    text-align: center;
    font-family: "Cinzel", serif;
    color: var(--paper);
  }
  .person-name { font-size: 26px; font-weight: 600; line-height: 30px; white-space: nowrap; }
  .person-title { font-size: 21px; font-weight: 400; letter-spacing: 1px; line-height: 26px; }
  .contacts {
    position: absolute;
    right: 38px;
    top: 322px;
    list-style: none;
    font-family: "Open Sans", sans-serif;
    font-size: 18px;
    color: var(--ink);
    text-align: right;
    line-height: 30px;
  }
  .contacts li { display: flex; justify-content: flex-end; align-items: center; gap: 8px; }
  .contacts svg { width: 15px; height: 15px; fill: var(--ink); }
  .address {
    position: absolute;
    left: 44px;
    top: 420px;
    font-family: "Open Sans", sans-serif;
    font-style: normal;
    font-size: 19px;
    line-height: 34px;
    color: var(--ink);
  }
</style>
</head>
<body>
<main class="canvas">

  <section class="card card-back" aria-label="Card back">
    <div class="back-mark"></div>
    <div class="back-name">HARBORLINE RENEWAL</div>
    <p class="tagline">Specializing in Water Damage Restoration</p>
  </section>

  <section class="card card-front" aria-label="Card front">
    <svg class="front-art" viewBox="0 0 880 503" aria-hidden="true">
      <path fill="var(--sky)" d="M0,430 C200,372 440,350 620,336 C740,324 830,252 880,200 L880,503 L0,503 Z"/>
      <path fill="var(--ocean)" d="M100,380 C300,262 540,228 790,222 C775,300 650,325 470,332 C300,342 190,356 100,380 Z"/>
    </svg>

    <div class="front-mark"></div>
    <div class="company-name">HARBORLINE RENEWAL</div>

    <div class="person">
      <div class="person-name">Darnell Quisby</div>
      <div class="person-title">Title</div>
    </div>

    <ul class="contacts">
      <li>
        <svg viewBox="0 0 16 16" aria-hidden="true"><path d="M3.5 1.5l2.5 0 1 3.5-1.6 1.2a8 8 0 0 0 4.4 4.4L11 9l3.5 1v2.5c0 1-1 2-2 2C6.5 14.5 1.5 9.5 1.5 3.5c0-1 1-2 2-2z"/></svg>
        555-318-2046
      </li>
      <li>
        <svg viewBox="0 0 16 16" aria-hidden="true"><path d="M1 3h14v10H1z M2.5 4.5L8 9l5.5-4.5v-0.5h-11z" fill-rule="evenodd"/></svg>
        Darnell@HarborlineRenewal.example
      </li>
      <li>
        <svg viewBox="0 0 16 16" aria-hidden="true"><circle cx="8" cy="8" r="7" fill="none" stroke="var(--ink)" stroke-width="1.6"/><path d="M1 8h14M8 1c-3 3.5-3 10.5 0 14M8 1c3 3.5 3 10.5 0 14" fill="none" stroke="var(--ink)" stroke-width="1.2"/></svg>
        www.HarborlineRenewal.example
      </li>
    </ul>

    <address class="address">
      Street Name, City Name<br>
      Zipcode-12345
    </address>
  </section>

</main>
</body>
</html>
```